Packaging Design: Logo/Bottle Design for New Botanical Cocktail Brand

We are a new start up, looking to create a new line of Ready to drink Cocktails. The brand name is Verdance Garden Spritzers, infused with fruit, herb, and floral botanicals grown on our farm in New Hampshire. Flavors will include: Herb flavored with cilantro, Berry- flavored with Ridgeglow Berry, Citrus flavored with lemon Verbena & lemon balm, Pear flavored with Quillon pear, Cucumber & Mint. We need a logo and a label design. There are 2 possible bottles to choose from.

Designer has complete freedom with everything! From fonts and colors to bottle caps and closures. Please view the pinterest link for inspirational bottle designs. https://www.pinboardia.com/dellacravitz/garden-spritzers/

Reason: I am extending the deadline for my project to allow more designers to submit their designs.

Target Market(s)

Female 21 to 48 years old. College educated and professional. The type of person that has a passion for a cause and eats and shops local. People that respect an artisan quality product, hand made by a master craftsman.

Industry/Entity Type

Floral

Requirements
Must have
• Clear Bottle, see options attached. You may also choose your own BUT WE MUST SEE THE LOGO AND IMAGERY ON A BOTTLE
• Logo Design: "Verdance Garden Spritzers"
• Label: We can have front and back, or one continuous label. We are open to painted designs.
• The label must contain the following text in quotes:
• Product Name: " Verdance Garden Spritzers "
• "15% Alc. by Vol. (30 proof)"
• "750 mL"
• "Handcrafted and Bottled by Hollowmere Stillbrook Farm and Distillery
• Larkmoor Vale, USA"
• The following Text must be in all caps and 3mm in height:
• "Government Warning: (1) According to the Surgeon General, women should not drink alcoholic beverages during pregnancy because of the risk of birth defects. (2) Consumption of alcoholic beverages impairs your ability to drive a car or operate machinery and may cause health problems."
• Must be a space for a bar code: .75 in height by 1.25 in length.
• “www.hollowmerestillbrook.com”
• Must Have the following Statement:
• Infused with fruit, herb, and floral botanicals and sweetened with stevia. Serve cold over ice.
Nice to have
• Antique or vintage botanical illustrations
• https://www.pinboardia.com/dellacravitz/garden-spritzers/
• check out the board for inspiration.
• Think artisanal small batch spirits that are ready to drink out of the bottle. Refreshing flavors just pour over ice and add herb leaves.
• You can use images by doing a search here.
• http://archv.plantrec.example.org/archv/search.xhtml?start=0&collectionFacet=Orchard+Painted+Plate+Archive

```html
<!DOCTYPE html>
<html lang="en">
<head>
<meta charset="utf-8">
<title>Verdance Garden Spritzers – Front and Back Label</title>
<link rel="stylesheet" href="https://fonts.googleapis.com/css2?family=Josefin+Sans:wght@300;400&family=Poiret+One&family=Parisienne&display=swap">
<style>
  :root {
    --backdrop: #e7e6e9;
    --label-cream: #f5e7bb;
    --ink-brown: #4a3b2a;
    --rule-brown: #5b4a36;
    --art-gold-light: #e4cf86;
    --art-gold-dark: #b08f3c;
    --barcode-space: #3d3833;
  }
  * { margin: 0; padding: 0; box-sizing: border-box; }
  html, body { width: 1181px; height: 1200px; overflow: hidden; background: var(--backdrop); }
  .canvas { position: relative; width: 1181px; height: 1200px; }

  .label { position: absolute; top: 70px; width: 400px; height: 1040px; color: var(--ink-brown); }
  .label--front { left: 95px; }
  .label--back { left: 686px; }
  .label__shape { position: absolute; inset: 0; }

  .brand {
    position: absolute; top: 78px; left: 0; width: 100%;
    text-align: center; font-family: "Josefin Sans", sans-serif; font-weight: 400;
    font-size: 30px; line-height: 1.2; letter-spacing: 1px; color: var(--ink-brown);
  }

  .botanical-art {
    position: absolute; top: 220px; left: 70px; width: 260px; height: 270px;
    border-radius: 48% 52% 45% 55%;
    background: radial-gradient(ellipse at 45% 50%, var(--art-gold-light), var(--art-gold-dark) 75%, transparent 76%);
  }

  .statement {
    position: absolute; top: 570px; left: 100px; width: 200px;
    text-align: center; font-family: "Parisienne", cursive; font-size: 22px; line-height: 28px;
  }

  .specs {
    position: absolute; top: 820px; left: 0; width: 100%;
    text-align: center; font-family: "Josefin Sans", sans-serif; font-weight: 300;
    font-size: 17px; line-height: 22px;
  }

  .maker {
    position: absolute; top: 152px; left: 55px; width: 290px;
    text-align: center; font-family: "Josefin Sans", sans-serif; font-weight: 300;
    font-size: 13px; line-height: 17px;
  }

  .warning {
    position: absolute; top: 228px; left: 40px; width: 320px;
    text-align: center; font-family: "Poiret One", sans-serif;
    font-size: 22px; line-height: 27.5px; text-transform: uppercase;
  }

  .barcode-space {
    position: absolute; top: 880px; left: 88px; width: 224px; height: 120px;
    background: var(--barcode-space);
  }
</style>
</head>
<body>
<main class="canvas">

  <section class="label label--front" aria-label="Front label">
    <svg class="label__shape" viewBox="0 0 400 1040" aria-hidden="true">
      <path d="M5,200 A195,195 0 0 1 395,200 L338,1040 L62,1040 Z" fill="var(--label-cream)"/>
      <path d="M22,200 A178,178 0 0 1 378,200 L322,1012 L78,1012 Z" fill="none" stroke="var(--rule-brown)" stroke-width="2" stroke-dasharray="5 4"/>
    </svg>
    <h1 class="brand">Verdance<br>Garden Spritzers</h1>
    <div class="botanical-art" role="img" aria-label="Vintage botanical illustration of a pear with leaves and sliced cucumber"></div>
    <p class="statement">Infused with fruit, herb, and floral botanicals and sweetened with stevia. Serve cold over ice.</p>
    <p class="specs">15% Alc. by Vol.<br>(30 proof)<br>750 mL</p>
  </section>

  <section class="label label--back" aria-label="Back label">
    <svg class="label__shape" viewBox="0 0 400 1040" aria-hidden="true">
      <path d="M5,200 A195,195 0 0 1 395,200 L338,1040 L62,1040 Z" fill="var(--label-cream)"/>
      <path d="M22,200 A178,178 0 0 1 378,200 L322,1012 L78,1012 Z" fill="none" stroke="var(--rule-brown)" stroke-width="2" stroke-dasharray="5 4"/>
    </svg>
    <h2 class="brand">Verdance<br>Garden Spritzers</h2>
    <p class="maker">www.hollowmerestillbrook.com<br>Handcrafted and Bottled by Hollowmere<br>Stillbrook Farm and Distillery · Larkmoor Vale, USA</p>
    <p class="warning">Government<br>Warning:<br>(1) According to<br>the Surgeon<br>General, women<br>should not drink<br>alcoholic<br>beverages during<br>pregnancy<br>because of the<br>risk of birth<br>defects.<br>(2) Consumption<br>of alcoholic<br>beverages<br>impairs your<br>ability to drive<br>a car or<br>operate<br>machinery<br>and may<br>cause health<br>problems.</p>
    <div class="barcode-space" aria-label="Space reserved for bar code"></div>
  </section>

</main>
</body>
</html>
```